Brightfern Care Alliance Flirvo Ads

We want an ad created for the gay dating app flirvo. The size is 300x250. We want the ad to be sexy, with a shirtless man. We are advertising our free HIV and PrEP services. We are open to slogans about maybe "Bringing HIV and PrEP To You"
"Free PrEP and HIV Management"
Open to ideas.

We also offer through the Cedarline Relief Fund
Copay Assistance, Insurance Premium Assistance, Free Medical Services, etc
Our website is bfcanj.org

I do want the ad to have a Book Now Button

Gay sexually active males

```html
<!DOCTYPE html>
<html lang="en">
<head>
<meta charset="utf-8">
<title>Brightfern Care Alliance – Free PrEP &amp; HIV Management</title>
<link rel="stylesheet" href="https://fonts.googleapis.com/css2?family=Montserrat:wght@400;600;700;800&display=swap">
<style>
  :root{
    --page:#9a9a9a;
    --ad-bg:#262626;
    --ad-band:#2b2b2b;
    --white:#ffffff;
    --orange:#ff6a1a;
    --blue:#1577ff;
    --violet:#7a35f0;
    --magenta:#c640ef;
    --pink:#ff3fc4;
    --coral:#ff6a3a;
    --outline:#ff86b0;
    --skin-light:#c07a4c;
    --skin-dark:#8a4a2a;
    --shorts:#9cc6ec;
  }
  html,body{margin:0;padding:0;width:1200px;height:1200px;overflow:hidden;background:var(--page);}
  .stage{position:relative;width:1200px;height:1200px;}
  .ad{
    position:absolute;left:189px;top:209px;width:1404px;height:1190px;
    transform:scale(0.6211);transform-origin:0 0;
    background:var(--ad-bg);overflow:hidden;
    font-family:"Montserrat",sans-serif;
  }
  .ad__band{position:absolute;left:0;width:100%;background:var(--ad-band);}
  .ad__band--top{top:0;height:50px;}
  .ad__band--bottom{bottom:0;height:62px;}
  .ad__art{position:absolute;left:0;top:0;}
  .model-photo{
    position:absolute;left:940px;top:0;width:464px;height:1190px;
    background:linear-gradient(180deg,var(--skin-light) 0%,var(--skin-dark) 80%,var(--shorts) 86%,var(--shorts) 100%);
    border-left:14px solid var(--outline);
    box-sizing:border-box;
  }
  .brand{position:absolute;left:80px;top:130px;display:flex;align-items:center;gap:26px;}
  .brand__dot{width:110px;height:110px;border-radius:50%;background:var(--magenta);flex:none;}
  .brand__name{color:var(--white);font-weight:700;font-size:44px;letter-spacing:5px;line-height:1.1;text-transform:uppercase;}
  .tagline{position:absolute;left:43px;top:322px;margin:0;color:var(--white);font-weight:400;font-size:37px;line-height:1;}
  .tagline__you{color:var(--orange);font-weight:700;}
  .headline{position:absolute;left:0;top:0;margin:0;font-weight:800;}
  .headline__line{
    position:absolute;left:40px;display:block;width:860px;white-space:nowrap;line-height:1;
    background:linear-gradient(90deg,var(--blue) 0%,var(--violet) 30%,var(--magenta) 48%,var(--pink) 62%,var(--coral) 80%,var(--coral) 100%);
    -webkit-background-clip:text;background-clip:text;color:transparent;
  }
  .headline__line--free{top:380px;font-size:136px;letter-spacing:-1px;}
  .headline__line--prep{top:489px;font-size:140px;letter-spacing:-2px;}
  .headline__line--manage{top:607px;font-size:106px;letter-spacing:-1px;}
  .book-btn{
    position:absolute;left:161px;top:854px;width:434px;height:76px;
    background:linear-gradient(90deg,#3f7bff 0%,#b85cf0 55%,#ff4f98 100%);
    color:var(--white);font-weight:600;font-size:26px;letter-spacing:6px;
    display:flex;align-items:center;justify-content:center;text-decoration:none;
  }
</style>
</head>
<body>
<div class="stage">
  <div class="ad">
    <div class="ad__band ad__band--top"></div>
    <div class="ad__band ad__band--bottom"></div>

    <svg class="ad__art" viewBox="0 0 1404 1190" width="1404" height="1190" aria-hidden="true">
      <defs>
        <linearGradient id="arcGrad" x1="0" y1="0" x2="1" y2="0">
          <stop offset="0" stop-color="#a63cf0"/>
          <stop offset="0.55" stop-color="#ff45d2"/>
          <stop offset="1" stop-color="#ff5a9a"/>
        </linearGradient>
      </defs>
      <path d="M290,1190 C520,1060 760,990 1000,960 L1404,950 L1404,1190 Z" fill="#000"/>
      <path d="M290,1190 C520,1060 760,990 1000,960 L1100,955" fill="none" stroke="url(#arcGrad)" stroke-width="26"/>
    </svg>

    <div class="model-photo" role="img" aria-label="Photo of a shirtless man in light blue underwear, hands behind his head"></div>

    <div class="brand">
      <span class="brand__dot"></span>
      <span class="brand__name">Brightfern<br>Care Alliance</span>
    </div>

    <p class="tagline">Bringing HIV and PrEP To <span class="tagline__you">You</span></p>

    <h1 class="headline">
      <span class="headline__line headline__line--free">FREE</span>
      <span class="headline__line headline__line--prep">PrEP &amp; HIV</span>
      <span class="headline__line headline__line--manage">MANAGEMENT</span>
    </h1>

    <svg class="ad__art" viewBox="0 0 1404 1190" width="1404" height="1190" aria-hidden="true">
      <path d="M12,762 C200,748 600,744 830,756 C870,762 876,784 836,790 C600,802 250,806 40,800 C14,796 2,770 12,762 Z" fill="var(--white)"/>
    </svg>

    <a class="book-btn" href="#">BOOK NOW</a>
  </div>
</div>
</body>
</html>
```